Clean business card with logo provided

I want a card that will stand out among the masses. I need the color and image to show professionalism and yet have a family appeal showing that I only deal with win/win scenarios. The back of the card will be used to take notes about the individual so I can use that in my database entry. I like modern design but need professionalism in it also. It needs to fit my "clean, safe, and affordable housing" motto. I need to be able to write on the file and update the card details for my employees.

Target Market(s)

Investors looking to make investment income through real estate

Industry/Entity Type

Real Estate

Contact Information for Business Card

Brent Kovalich
blank address, city, st, zip code
480-555-3174
brentkovalich@ridgeworthrentals.example
www.ridgeworthrentals.example

Font styles to use
Sans Serif

Requirements
Must have
• I would like the back of the card to have lines for info. example
• Met/Visited: Date:
• Interets:
Nice to have
• I want the cards color to match the logo background color. Font with details to be san serif and black. I want the card rectangular with square corners. Standard business card size. I would like to see cards designed with both images to see which i prefer more.

```html
<!DOCTYPE html>
<html lang="en">
<head>
<meta charset="utf-8">
<title>Ridgeworth Rentals LLC – Business Card</title>
<link href="https://fonts.googleapis.com/css2?family=Open+Sans:wght@400;600;700&display=swap" rel="stylesheet">
<style>
  :root {
    --stage: #000000;
    --paper: #ffffff;
    --brand: #0bb5cc;
    --ink: #111111;
    --rule: #222222;
  }
  * { margin: 0; padding: 0; box-sizing: border-box; }
  html, body { width: 1200px; height: 900px; overflow: hidden; background: var(--stage); }
  body { position: relative; font-family: "Open Sans", Arial, sans-serif; }

  .card {
    position: absolute;
    top: 275px;
    width: 477px;
    height: 293px;
    background: var(--paper);
    overflow: hidden;
  }
  .card--front { left: 116px; border-radius: 0 50px 0 50px; }
  .card--back  { left: 622px; border-radius: 50px 0 50px 0; }

  .band { position: absolute; left: 0; width: 100%; height: 15px; background: var(--brand); }
  .band--top { top: 0; }
  .band--bottom { bottom: 0; }

  .front-content { position: absolute; inset: 0; text-align: center; }
  .holder-name {
    position: absolute; top: 29px; width: 100%;
    color: var(--brand); font-weight: 600; font-size: 17px; letter-spacing: 0.5px;
  }
  .company-name {
    position: absolute; top: 78px; width: 100%;
    color: var(--brand); font-weight: 600; font-size: 26px; letter-spacing: 2px;
  }
  .tagline {
    position: absolute; top: 136px; width: 100%;
    color: var(--brand); font-weight: 600; font-size: 8.5px;
  }
  .contact-list { position: absolute; top: 166px; width: 100%; list-style: none; }
  .contact-list li {
    display: flex; justify-content: center; align-items: center; gap: 5px;
    height: 20px; font-size: 13px; color: var(--ink);
  }
  .contact-list svg { width: 10px; height: 10px; fill: var(--brand); flex: none; }
  .address {
    position: absolute; top: 245px; width: 100%;
    font-size: 13px; color: var(--ink);
  }

  .note-field { position: absolute; left: 0; width: 100%; }
  .note-label {
    position: absolute; width: 100%; left: 0; text-align: center;
    padding-left: 0; color: var(--brand); font-weight: 600; font-size: 14px;
  }
  .note-line {
    position: absolute; left: 113px; width: 215px; height: 1.5px; background: var(--rule);
  }
</style>
</head>
<body>

  <section class="card card--front" aria-label="Card front">
    <div class="band band--top"></div>
    <div class="front-content">
      <p class="holder-name">BRENT KOVALICH</p>
      <p class="company-name">RIDGEWORTH RENTALS LLC</p>
      <p class="tagline">Providing clean, safe, and affordable housing</p>
      <ul class="contact-list">
        <li>
          <svg viewBox="0 0 10 10" aria-hidden="true"><path d="M2 0.5 L3.6 0.5 L4.2 3 L3 3.8 C3.6 5.2 4.8 6.4 6.2 7 L7 5.8 L9.5 6.4 L9.5 8 C9.5 9 8.8 9.5 8 9.5 C4 9.2 0.8 6 0.5 2 C0.5 1.2 1 0.5 2 0.5Z"/></svg>
          <span>480-555-3174</span>
        </li>
        <li>
          <svg viewBox="0 0 10 10" aria-hidden="true"><path d="M0.5 2 L9.5 2 L9.5 8.5 L0.5 8.5Z M1 2.5 L5 5.8 L9 2.5" stroke="#fff" stroke-width="0.8"/></svg>
          <span>brentkovalich@ridgeworthrentals.example</span>
        </li>
        <li>
          <svg viewBox="0 0 10 10" aria-hidden="true"><circle cx="5" cy="5" r="4.6"/></svg>
          <span>www.ridgeworthrentals.example</span>
        </li>
      </ul>
      <p class="address">12345, Address Goes Here Country Name, 123456</p>
    </div>
    <div class="band band--bottom"></div>
  </section>

  <section class="card card--back" aria-label="Card back, notes">
    <div class="band band--top"></div>
    <p class="note-label" style="top:55px">VISITED DATE:</p>
    <div class="note-line" style="top:103px"></div>
    <p class="note-label" style="top:123px">INTERETS:</p>
    <div class="note-line" style="top:169px"></div>
    <p class="note-label" style="top:191px">PROBLEMS:</p>
    <div class="note-line" style="top:236px"></div>
    <div class="band band--bottom"></div>
  </section>

</body>
</html>
```